Graphics Design of Physics Book

Hi
Size : 8" x 11.25"
We are education book Publication Company and would like to have book cover for "Physics" it has 4 volumes. All 4 having the same color scheme and design except the volume no.
Blue is my personal favorite but u can use any color. Want to have a band at the bottom of the cover to place our Logo “VORNA Education” a PDF of the same is attached, or you can place logo anywhere according to ur design.
I need “Physics” as title of the book to be visible prominently.
And volume and volume no. should also be Visible and eye catching I prefer a Graphic to enhance the Volume No.
A background pattern can also be a option (it should be vector form so that color can be change later)
Please do not offer any cut and paste design I need very professional presentation.
Volume and Number can be in metallic 3D (CMYK) effect.
only Professional presentation will get feedback.
I have provided a sample artwork for reference do not follow it but can be a reference what I needed !

Target Market(s)

Students Class 9th to 12th

Industry/Entity Type

Education

Font styles to use
Serif

Colors
3176b5
0555a3
85abd2
cadf82
abd036
9bcb3c

Requirements
Must have
• Eye catching.
• “Physics” as title of the book to be visible prominently.
• volume and volume no. should also be Visible and eye catching
• I prefer a Graphic to enhance the Volume No.
• Icons for
• 1. Questions and answers
• 2. Theory Notes
• 3. Tips & Tricks
• 4. Previous Year's Reference Questions
• 5. Covers Complete Syllabus
Nice to have
• decent seamless background or metallic 3d effect (not to be print in special Ink) design should only be in CMYK.
Should not have
• Physics related Pictures or Icons (Specially E=mc2) or any scientist photograph or I Need pure graphic design

```html
<!DOCTYPE html>
<html lang="en">
<head>
<meta charset="utf-8">
<title>Physics Vol 1 — Book Cover</title>
<link rel="stylesheet" href="https://fonts.googleapis.com/css2?family=Arvo:wght@700&family=Arimo:wght@400;700&display=swap">
<style>
  :root {
    --ink-deep: #05080f;
    --steel-blue: #1d3f6e;
    --brand-blue: #0555a3;
    --lime: #9bcb3c;
    --lime-light: #abd036;
    --white: #ffffff;
  }
  * { margin: 0; padding: 0; box-sizing: border-box; }
  html, body { width: 854px; height: 1200px; overflow: hidden; background: var(--ink-deep); }
  .cover {
    position: relative;
    width: 854px;
    height: 1200px;
    overflow: hidden;
    font-family: "Arimo", Arial, sans-serif;
    color: var(--white);
  }
  .cover__pattern {
    position: absolute;
    inset: 0;
    background:
      radial-gradient(ellipse 520px 340px at 380px 120px, #24497d 0%, rgba(36,73,125,0) 70%),
      radial-gradient(ellipse 300px 260px at 700px 520px, #1b3862 0%, rgba(27,56,98,0) 70%),
      linear-gradient(180deg, #112645 0%, #0b1a30 45%, #060c16 75%, #04070d 100%);
  }
  .cover__rule {
    position: absolute;
    top: 0; left: 0;
    width: 100%;
    height: 3px;
    background: var(--brand-blue);
  }
  .title {
    position: absolute;
    left: 58px;
    top: 22px;
    font-family: "Arvo", "Rockwell", serif;
    font-weight: 700;
    font-size: 196px;
    line-height: 1;
    letter-spacing: -9px;
    color: var(--white);
  }
  .volume {
    position: absolute;
    left: 498px;
    top: 238px;
    width: 356px;
    height: 132px;
    background: var(--lime);
    box-shadow: 0 4px 10px rgba(0,0,0,0.45);
  }
  .volume__label {
    position: absolute;
    left: 30px;
    top: 14px;
    font-family: "Arimo", Arial, sans-serif;
    font-size: 108px;
    line-height: 1;
    letter-spacing: -6px;
    color: var(--white);
  }
  .volume__number {
    position: absolute;
    left: 204px;
    top: 15px;
    width: 92px;
    height: 101px;
    background: var(--white);
    color: var(--lime);
    font-family: "Arimo", Arial, sans-serif;
    font-size: 96px;
    line-height: 101px;
    text-align: center;
  }
  .features {
    position: absolute;
    left: 40px;
    top: 1040px;
    display: flex;
    list-style: none;
  }
  .feature {
    width: 104px;
    display: flex;
    flex-direction: column;
    align-items: center;
    text-align: center;
  }
  .feature svg { width: 62px; height: 62px; }
  .feature__label {
    margin-top: 12px;
    font-size: 10.5px;
    font-weight: 700;
    line-height: 1.15;
    text-transform: uppercase;
  }
  .brand {
    position: absolute;
    left: 622px;
    top: 1060px;
    display: flex;
    align-items: center;
    gap: 10px;
    font-family: "Arimo", Arial, sans-serif;
    font-weight: 700;
    font-size: 22px;
    color: var(--white);
  }
  .brand__square { width: 18px; height: 18px; background: var(--white); }
</style>
</head>
<body>
<main class="cover">
  <div class="cover__pattern" role="img" aria-label="Dark blue metallic perforated hexagon mesh background"></div>
  <div class="cover__rule"></div>

  <h1 class="title">Physics</h1>

  <div class="volume">
    <span class="volume__label">Vol</span>
    <span class="volume__number">1</span>
  </div>

  <ul class="features">
    <li class="feature">
      <svg viewBox="0 0 62 62" aria-hidden="true">
        <ellipse cx="22" cy="24" rx="18" ry="15" fill="#fff"/>
        <path d="M12 36 L10 48 L22 38 Z" fill="#fff"/>
        <text x="22" y="31" text-anchor="middle" font-family="Arimo" font-weight="700" font-size="20" fill="#05080f">?</text>
        <ellipse cx="42" cy="34" rx="18" ry="14" fill="#05080f" stroke="#fff" stroke-width="3"/>
        <path d="M46 46 L50 56 L38 47 Z" fill="#fff"/>
        <rect x="35" y="27" width="13" height="12" fill="none" stroke="#fff" stroke-width="2"/>
        <path d="M37 32 L41 36 L50 25" fill="none" stroke="#fff" stroke-width="2.5"/>
      </svg>
      <span class="feature__label">Questions &amp;<br>Answers</span>
    </li>
    <li class="feature">
      <svg viewBox="0 0 62 62" aria-hidden="true">
        <rect x="8" y="10" width="38" height="48" fill="#fff"/>
        <rect x="12" y="14" width="30" height="40" fill="#05080f"/>
        <g stroke="#fff" stroke-width="2">
          <line x1="15" y1="21" x2="38" y2="21"/><line x1="15" y1="28" x2="38" y2="28"/>
          <line x1="15" y1="35" x2="34" y2="35"/><line x1="15" y1="42" x2="30" y2="42"/>
        </g>
        <path d="M52 6 L58 12 L34 42 L27 45 L29 37 Z" fill="#fff"/>
      </svg>
      <span class="feature__label">Theory<br>Notes</span>
    </li>
    <li class="feature">
      <svg viewBox="0 0 62 62" aria-hidden="true">
        <rect x="6" y="2" width="50" height="58" fill="#fff"/>
        <line x1="31" y1="2" x2="31" y2="16" stroke="#05080f" stroke-width="2"/>
        <circle cx="31" cy="32" r="11" fill="none" stroke="#05080f" stroke-width="2.5"/>
        <rect x="26" y="42" width="10" height="8" fill="#05080f"/>
      </svg>
      <span class="feature__label">Tips &amp;<br>Tricks</span>
    </li>
    <li class="feature">
      <svg viewBox="0 0 62 62" aria-hidden="true">
        <circle cx="24" cy="20" r="15" fill="none" stroke="#fff" stroke-width="4"/>
        <path d="M24 11 V20 H32" fill="none" stroke="#fff" stroke-width="3"/>
        <text x="46" y="34" font-family="Arimo" font-weight="700" font-size="16" fill="#fff">?</text>
        <text x="32" y="46" font-family="Arimo" font-weight="700" font-size="18" fill="#fff">?</text>
        <text x="18" y="60" font-family="Arimo" font-weight="700" font-size="20" fill="#fff">?</text>
      </svg>
      <span class="feature__label">Previous Year's<br>Reference<br>Questions</span>
    </li>
    <li class="feature">
      <svg viewBox="0 0 62 62" aria-hidden="true">
        <path d="M12 42 A22 22 0 0 1 36 10" fill="none" stroke="#fff" stroke-width="5"/>
        <path d="M50 22 A22 22 0 0 1 26 54" fill="none" stroke="#fff" stroke-width="5"/>
        <path d="M34 3 L44 10 L34 17 Z" fill="#fff"/>
        <path d="M28 47 L18 54 L28 61 Z" fill="#fff"/>
        <rect x="20" y="18" width="20" height="24" fill="#fff" transform="rotate(-20 30 30)"/>
      </svg>
      <span class="feature__label">Covers<br>Complete<br>Syllabus</span>
    </li>
  </ul>

  <div class="brand">
    <span class="brand__square"></span>
    <span class="brand__name">VORNA Education</span>
  </div>
</main>
</body>
</html>
```